Heron Loan Partners Business Card

We need a business card design for our mortgage servicing company. In addition to servicing the loans of homeowners, we help homeowners with purchasing their homes and any mortgage refinancing. We would like to see designs that use the colors in the logo attached below (gold-ish yellow and navy blue), and any other design you deem fit! The design should communicate a simpler life with smart mortgages provided by Heron.

```html
<!DOCTYPE html>
<html lang="en">
<head>
<meta charset="utf-8">
<title>Heron Loan Partners Business Card</title>
<link rel="stylesheet" href="https://fonts.googleapis.com/css2?family=Open+Sans:wght@400;600;700&display=swap">
<style>
  :root {
    --stage: #232323;
    --card-white: #f4f4f4;
    --gold: #dcac3c;
    --gold-light: #e6b942;
    --gold-deep: #c9982e;
    --navy: #2a2466;
    --ink: #1a1a1a;
    --paper-white: #ffffff;
  }
  * { box-sizing: border-box; margin: 0; padding: 0; }
  html, body { width: 1200px; height: 780px; overflow: hidden; }
  body {
    background: var(--stage);
    font-family: "Open Sans", Arial, sans-serif;
    position: relative;
  }
  .card {
    position: absolute;
    top: 247px;
    width: 500px;
    height: 286px;
    overflow: hidden;
    box-shadow: 0 14px 30px rgba(0,0,0,0.45);
  }
  .card--front { left: 70px; background: var(--card-white); }
  .card--back { left: 630px; }

  .front-band { position: absolute; inset: 0; }

  .brand {
    position: absolute;
    left: 280px;
    top: 48px;
    display: flex;
    align-items: center;
    gap: 10px;
  }
  .brand__dot {
    width: 16px; height: 16px;
    border-radius: 50%;
    background: var(--navy);
  }
  .brand__name {
    font-size: 34px;
    font-weight: 700;
    color: var(--gold);
    line-height: 1;
  }

  .person { position: absolute; left: 36px; top: 44px; }
  .person__name {
    font-size: 25px;
    font-weight: 700;
    line-height: 1.1;
  }
  .person__first { color: var(--gold); }
  .person__last { color: var(--navy); }
  .person__title {
    margin-top: 4px;
    margin-left: 22px;
    font-size: 12px;
    color: var(--ink);
  }

  .divider {
    position: absolute;
    left: 196px;
    top: 108px;
    width: 1.5px;
    height: 78px;
    background: var(--ink);
  }

  .contacts {
    position: absolute;
    left: 212px;
    top: 108px;
    list-style: none;
  }
  .contacts__item {
    display: flex;
    align-items: center;
    gap: 8px;
    font-size: 13px;
    line-height: 19px;
    color: var(--ink);
  }
  .contacts__icon { width: 11px; height: 11px; flex: none; }

  .address {
    position: absolute;
    left: 22px;
    bottom: 12px;
    font-size: 12px;
    line-height: 16px;
    color: var(--paper-white);
    letter-spacing: 0.2px;
  }

  .back-pattern {
    position: absolute;
    inset: 0;
    background: linear-gradient(120deg, var(--gold-deep) 0%, var(--gold-light) 60%, #ecc965 100%);
  }
</style>
</head>
<body>

  <section class="card card--front" aria-label="Business card front">
    <svg class="front-band" viewBox="0 0 500 286" width="500" height="286" aria-hidden="true">
      <path d="M0,150 Q260,250 500,282 L500,286 L0,286 Z" fill="var(--gold)"/>
      <path d="M14,140 Q262,238 490,270" fill="none" stroke="var(--navy)" stroke-width="2.5" stroke-linecap="round"/>
    </svg>

    <div class="brand">
      <span class="brand__dot"></span>
      <span class="brand__name">Heron</span>
    </div>

    <div class="person">
      <p class="person__name"><span class="person__first">Lena</span> <span class="person__last">Varkova</span></p>
      <p class="person__title">Managing Director</p>
    </div>

    <span class="divider"></span>

    <ul class="contacts">
      <li class="contacts__item">
        <svg class="contacts__icon" viewBox="0 0 12 12" aria-hidden="true"><path d="M3 1 L5 3.5 L4 5 Q5 7 7 8 L8.5 7 L11 9 L9.5 11 Q4 10.5 1 3 Z" fill="var(--gold)"/></svg>
        (555) 014-2758
      </li>
      <li class="contacts__item">
        <svg class="contacts__icon" viewBox="0 0 12 12" aria-hidden="true"><rect x="2" y="1" width="8" height="10" rx="1.5" fill="var(--gold)"/><rect x="3.5" y="2.5" width="5" height="5" fill="var(--card-white)"/></svg>
        (555) 014-2758
      </li>
      <li class="contacts__item">
        <svg class="contacts__icon" viewBox="0 0 12 12" aria-hidden="true"><rect x="1" y="2.5" width="10" height="7" rx="1" fill="var(--gold)"/><path d="M1.5 3 L6 6.5 L10.5 3" fill="none" stroke="var(--card-white)" stroke-width="1"/></svg>
        info@heronloans.com
      </li>
      <li class="contacts__item">
        <svg class="contacts__icon" viewBox="0 0 12 12" aria-hidden="true"><circle cx="6" cy="6" r="5" fill="var(--gold)"/><path d="M1 6 H11 M6 1 Q3 6 6 11 M6 1 Q9 6 6 11" fill="none" stroke="var(--card-white)" stroke-width="0.8"/></svg>
        www.heronloans.com
      </li>
    </ul>

    <p class="address">1840 Lakeside Ave. Suite 300 Riverton, TX 75001</p>
  </section>

  <section class="card card--back" aria-label="Business card back">
    <div class="back-pattern" role="img" aria-label="Repeating pattern of the Heron Loan Partners brand mark on gold"></div>
  </section>

</body>
</html>
```